Bramblewick Forage Business Cards

I need a business card with my logo, number, Facebook account, and some information about what I am selling. Green card with logo on the front. 555-214-8392 phone number, @bramblewickforage Facebook, •Orchardgrass Hay •Alfalfa Hay •Mixed Grass Hay , and “Premium Quality Hay” all written on the back.

Target Market(s)

Hay

Contact Information for Business Card

Phone number, Facebook, different types of hay.

Colors
00AB8E
00BBA5
67D7C9
C6EFE9
E9F9F6

```html
<!DOCTYPE html>
<html lang="en">
<head>
<meta charset="utf-8">
<title>Bramblewick Forage Business Cards</title>
<link href="https://fonts.googleapis.com/css2?family=Roboto:wght@400;500;700;900&display=swap" rel="stylesheet">
<style>
  :root {
    --page: #d9d9d9;
    --card: #1f1f1f;
    --green: #00a651;
    --white: #ffffff;
  }
  * { box-sizing: border-box; margin: 0; padding: 0; }
  html, body { width: 1200px; height: 800px; overflow: hidden; }
  body {
    background: var(--page);
    font-family: "Roboto", Arial, sans-serif;
    color: var(--white);
    position: relative;
  }
  .card {
    position: absolute;
    width: 540px;
    height: 310px;
    background: var(--card);
    border-radius: 20px;
    box-shadow: 0 14px 30px rgba(0,0,0,0.25);
    overflow: hidden;
  }
  .card-front { left: 40px; top: 245px; }
  .card-back { left: 620px; top: 245px; }

  /* front */
  .front-mark {
    position: absolute;
    left: 30px; top: 65px;
    width: 180px; height: 180px;
    display: flex; align-items: center; justify-content: center;
  }
  .front-mark .mark-circle {
    position: absolute; inset: 0;
    border-radius: 50%;
    background: var(--green);
  }
  .front-mark .mark-name {
    position: relative;
    font-weight: 700;
    font-size: 22px;
    line-height: 1.15;
    text-align: center;
    color: var(--white);
  }
  .front-contact {
    position: absolute;
    left: 236px; top: 120px;
    white-space: nowrap;
  }
  .front-phone {
    font-weight: 900;
    font-size: 34px;
    letter-spacing: 0.3px;
    white-space: nowrap;
  }
  .front-social {
    display: flex; align-items: center; gap: 9px;
    margin-top: 8px;
    font-size: 19px;
    font-weight: 400;
    white-space: nowrap;
  }
  .social-dot {
    width: 20px; height: 20px; border-radius: 50%;
    background: var(--green);
    flex: none;
  }

  /* back */
  .back-header {
    position: absolute;
    left: 40px; top: 70px;
    display: flex; align-items: center; gap: 22px;
  }
  .back-mark {
    width: 110px; height: 110px; border-radius: 50%;
    background: var(--green);
    flex: none;
  }
  .back-name {
    font-weight: 700;
    font-size: 33px;
    white-space: nowrap;
  }
  .back-phone {
    font-weight: 900;
    font-size: 44px;
    margin-top: 4px;
    letter-spacing: 0.5px;
    white-space: nowrap;
  }
  .hay-list {
    position: absolute;
    left: 30px; right: 20px; bottom: 40px;
    list-style: none;
    display: flex; flex-wrap: nowrap; align-items: center;
    font-size: 11.5px;
    font-weight: 500;
    white-space: nowrap;
  }
  .hay-list li { display: flex; align-items: center; }
  .hay-list li + li::before {
    content: "";
    width: 6px; height: 6px; border-radius: 50%;
    background: var(--green);
    margin: 0 6px;
  }
</style>
</head>
<body>
  <section class="card card-front" aria-label="Card front">
    <div class="front-mark">
      <span class="mark-circle"></span>
      <span class="mark-name">Bramblewick<br>Forage</span>
    </div>
    <div class="front-contact">
      <p class="front-phone">555-214-8392</p>
      <p class="front-social"><span class="social-dot"></span>@bramblewickforage</p>
    </div>
  </section>

  <section class="card card-back" aria-label="Card back">
    <div class="back-header">
      <span class="back-mark"></span>
      <div>
        <p class="back-name">Bramblewick Forage</p>
        <p class="back-phone">555-214-8392</p>
      </div>
    </div>
    <ul class="hay-list">
      <li>Orchardgrass Hay</li>
      <li>Alfalfa Hay</li>
      <li>Mixed Grass Hay, &amp; Premium Quality Hay</li>
    </ul>
  </section>
</body>
</html>
```